BRISKEL Need a luxury modern business card designed.

Need a luxury modern business card designed. refer to the uploaded files for the company name and logo in the zip file under source files. i will making my descion on monday. so please send in before then so if we need to edit we will have the time. we have a trade show coming up and im on a deadline for printer.

Target Market(s)

high end clients

Contact Information for Business Card

Company nAme and logo. Tobias Fennick Co-Founder / Project Manager Office # 555-318-7094 Cell # 555-642-1586 BRISKEL.CA Tobias@briskel-example.ca

Font styles to use
Other font styles liked:
• Modern

Requirements
Must have
• Company name and logo, contact info, using the black, gold and white color scheme.

```html
<!DOCTYPE html>
<html lang="en">
<head>
<meta charset="UTF-8">
<title>BRISKEL Business Card</title>
<link href="https://fonts.googleapis.com/css2?family=Montserrat:wght@300;600&family=Exo+2:wght@400&display=swap" rel="stylesheet">
<style>
  :root {
    --backdrop: #1a1a1a;
    --card-dark: #2d2d2d;
    --card-light: #ffffff;
    --gold: #a8986a;
    --ink: #2a2a2a;
    --white: #f4f4f4;
  }
  * { margin: 0; padding: 0; box-sizing: border-box; }
  html, body {
    width: 1200px; height: 900px; overflow: hidden;
    background: var(--backdrop);
  }
  .canvas { position: relative; width: 1200px; height: 900px; }
  .card {
    position: absolute; left: 285px; width: 630px; height: 360px;
    overflow: hidden;
  }
  .card--front { top: 70px; background: var(--card-dark); }
  .card--back { top: 470px; background: var(--card-light); }

  .brand {
    position: absolute; left: 0; right: 0;
    display: flex; align-items: center; justify-content: center; gap: 14px;
    font-family: "Montserrat", sans-serif; font-weight: 300;
    letter-spacing: 10px;
  }
  .brand__mark { width: 14px; height: 14px; border: 2px solid currentColor; }
  .card--front .brand { top: 155px; font-size: 36px; color: var(--white); }
  .card--back .brand { top: 52px; font-size: 32px; color: var(--ink); }

  .divider {
    position: absolute; left: 65px; right: 40px; top: 140px;
    height: 1.5px; background: var(--gold);
  }
  .accent-tab {
    position: absolute; left: 0; top: 166px; width: 8px; height: 36px;
    background: var(--gold);
  }
  .person { position: absolute; left: 42px; top: 160px; }
  .person__name {
    font-family: "Montserrat", sans-serif; font-weight: 600;
    font-size: 27px; color: var(--gold); letter-spacing: 0.5px;
    text-transform: uppercase;
  }
  .person__role {
    font-family: "Exo 2", sans-serif; font-size: 19px; color: var(--ink);
    margin-top: 2px;
  }

  .contact {
    position: absolute; right: 26px; top: 208px;
    list-style: none;
    font-family: "Exo 2", sans-serif; font-size: 19px; color: var(--ink);
  }
  .contact__item {
    display: flex; align-items: center; justify-content: flex-end;
    gap: 14px; height: 27px;
  }
  .contact__icon { width: 18px; height: 18px; }
  .contact__highlight { color: var(--gold); }

  .base-bands { position: absolute; left: 0; bottom: 0; }
</style>
</head>
<body>
<main class="canvas">

  <section class="card card--front" aria-label="Card front">
    <div class="brand"><span class="brand__mark"></span><span>BRISKEL</span></div>
  </section>

  <section class="card card--back" aria-label="Card back">
    <div class="brand"><span class="brand__mark"></span><span>BRISKEL</span></div>
    <div class="divider"></div>
    <div class="accent-tab"></div>

    <div class="person">
      <h1 class="person__name">Tobias Fennick</h1>
      <p class="person__role">Co-Founder | Project Manager</p>
    </div>

    <ul class="contact">
      <li class="contact__item">555-318-7094
        <svg class="contact__icon" viewBox="0 0 20 20" fill="none" stroke="var(--gold)" stroke-width="1.5">
          <circle cx="10" cy="10" r="8"/>
          <path d="M7 6.5c0 3.5 3 6.5 6.5 6.5l0.5-1.8-2-0.8-0.9 0.9c-1-0.5-1.9-1.4-2.4-2.4l0.9-0.9-0.8-2z"/>
        </svg>
      </li>
      <li class="contact__item">555-642-1586
        <svg class="contact__icon" viewBox="0 0 20 20" fill="none" stroke="var(--gold)" stroke-width="1.5">
          <rect x="6" y="2" width="8" height="16" rx="1.5"/>
          <line x1="9" y1="15" x2="11" y2="15"/>
        </svg>
      </li>
      <li class="contact__item">Tobias@briskel-example.ca
        <svg class="contact__icon" viewBox="0 0 20 20" fill="none" stroke="var(--gold)" stroke-width="1.5">
          <rect x="2" y="5" width="16" height="11"/>
          <path d="M2 5l8 6 8-6"/>
        </svg>
      </li>
      <li class="contact__item"><span>www.<span class="contact__highlight">briskel</span>.ca</span>
        <svg class="contact__icon" viewBox="0 0 20 20" fill="none" stroke="var(--gold)" stroke-width="1.5">
          <circle cx="10" cy="10" r="8"/>
          <ellipse cx="10" cy="10" rx="3.5" ry="8"/>
          <line x1="2" y1="10" x2="18" y2="10"/>
        </svg>
      </li>
    </ul>

    <svg class="base-bands" width="630" height="40" viewBox="0 0 630 40" aria-hidden="true">
      <polygon points="30,4 352,4 374,40 50,40" fill="var(--gold)"/>
      <polygon points="364,22 630,22 630,40 374,40" fill="var(--ink)"/>
    </svg>
  </section>

</main>
</body>
</html>
```